Military and tactical gear supply company needs web design

We need a web design for a company called U.S. Torvane. We provide quality tactical equipment to military and law enforcement. This is an e-commerce business and we primarily market ourselves on social media. Our key products are backpacks, military-style belts, and tactical flashlights. The gear we sell is not yet widely known about, but is on par with the state-of-the-art products in this field. We want the website to convey the message of quality, durability, and reliability. We use the word "kinetic" because the customers in this field are very "action-oriented" and we would like that idea to be communicated in the web site as well. The primary demographic is men in their 20's-30's, so the web site should have a masculine feel to it. Attached is the logo and color scheme.

```html
<!DOCTYPE html>
<html lang="en">
<head>
<meta charset="utf-8">
<title>U.S. Torvane – Tactical Gear</title>
<link href="https://fonts.googleapis.com/css2?family=Titillium+Web:wght@300;400;600;700;900&display=swap" rel="stylesheet">
<style>
:root{
  --red:#b3232a;
  --red-dark:#8f1b20;
  --steel:#3f6a84;
  --ink:#1f1d1d;
  --text:#333;
  --muted:#6d6d6d;
  --paper:#eeeeee;
  --white:#fff;
  --star:#f2a900;
  --footer:#1c1514;
}
*{box-sizing:border-box;margin:0;padding:0}
html,body{width:1200px;height:3525px;overflow:hidden}
body{font-family:"Titillium Web",sans-serif;color:var(--text);background:var(--paper);position:relative}
.abs{position:absolute}
a{color:inherit;text-decoration:none}

/* top bar */
.topbar{top:0;left:0;width:1200px;height:33px;background:var(--white)}
.contact-item{top:3px;font-size:12px;color:#555;display:flex;align-items:center;gap:7px;letter-spacing:.3px}
.search{left:435px;top:0;width:441px;height:33px;border:1px solid #bbb;background:#fff;font-size:12px;color:#888;padding:7px 15px}
.search-btn{left:876px;top:0;width:31px;height:33px;background:var(--red);display:flex;align-items:center;justify-content:center}
.account{left:907px;top:0;width:181px;height:33px;background:var(--ink);color:#fff;font-size:10px;display:flex;align-items:center;justify-content:space-around;padding:0 10px;letter-spacing:.2px}
.account span{display:flex;align-items:center;gap:5px}

/* header */
.header{top:33px;left:0;width:1200px;height:82px;background:var(--white);border-bottom:1px solid #ddd}
.brand{left:110px;top:20px;display:flex;align-items:center;gap:10px;font-weight:900;font-size:34px;color:var(--ink);letter-spacing:1px;line-height:1}
.brand i{display:block;width:14px;height:14px;background:var(--red)}
.brand-sub{left:222px;top:54px;font-size:12px;font-weight:600;color:#222;font-style:normal}
.nav{top:35px;font-size:14px;letter-spacing:1px;color:#222;font-weight:400}
.nav.active{color:var(--red)}

/* hero */
.hero{top:115px;left:0;width:1200px;height:528px;background:linear-gradient(110deg,#2b2b2b 0%,#4a4a4a 45%,#3a2220 60%,#2a2626 100%)}
.hero-title{left:107px;top:262px;font-size:82px;font-weight:700;color:#fff;letter-spacing:-1px;line-height:1}
.btn{display:flex;align-items:center;justify-content:center;background:var(--red);color:#fff;font-size:14px;font-weight:600;letter-spacing:.3px;text-transform:uppercase}
.hero-btn{left:111px;top:389px;width:137px;height:36px}

/* section titles */
.section-title{left:0;width:1200px;text-align:center;font-size:42px;font-weight:700;color:var(--red);line-height:1;text-transform:uppercase}
.section-title em{font-style:normal;color:var(--steel)}
.section-sub{left:0;width:1200px;text-align:center;font-size:13px;line-height:19px;color:#222;letter-spacing:.4px}

/* products */
.products{top:643px;left:0;width:1200px;height:638px;background:var(--paper)}
.product{top:843px;width:211px;height:301px;background:var(--white);border-right:1px solid #e6e6e6;text-align:center}
.product-img{position:absolute;left:35px;top:18px;width:141px;height:120px;border-radius:6px}
.product-name{position:absolute;left:0;top:175px;width:100%;font-size:14px;line-height:19px;color:#333;letter-spacing:.3px}
.stars{position:absolute;left:0;top:222px;width:100%;display:flex;justify-content:center;gap:8px}
.price{position:absolute;left:0;top:255px;width:100%;font-size:21px;font-weight:600;color:#222;letter-spacing:.5px}
.badge{position:absolute;left:20px;top:17px;background:var(--red);color:#fff;font-size:8px;padding:2px 12px;font-weight:600}
.arrow{top:978px}

/* about */
.about{top:1281px;left:0;width:1200px;height:604px;background:linear-gradient(90deg,#1d1a1a 0%,#262222 35%,#3b4654 60%,#4d5562 100%)}
.about-head{left:111px;font-size:40px;font-weight:700;line-height:1;text-transform:uppercase}
.about-text{left:111px;top:1491px;width:476px;font-size:15px;line-height:26.6px;color:#e8e8e8;text-align:justify;font-weight:400}
.about-btn{left:111px;top:1763px;width:137px;height:37px}

/* testimonials */
.testimonials{top:1885px;left:0;width:1200px;height:608px;background:var(--paper)}
.quote{top:2100px;width:313px;height:257px;background:var(--white);border-radius:4px;padding:28px 24px}
.quote p{font-size:12.5px;line-height:22.5px;color:#666;text-align:justify}
.person{position:absolute;left:28px;top:157px;display:flex;align-items:center;gap:14px}
.avatar{width:62px;height:62px;border-radius:50%;background:linear-gradient(160deg,#c9ced4,#6f7882)}
.person b{display:block;font-size:15px;font-weight:700;color:#222;line-height:18px}
.person small{display:block;font-size:13px;color:#666;line-height:16px}
.dots{top:2394px;left:560px;display:flex;gap:10px}
.dots span{width:12px;height:12px;border-radius:50%;border:2px solid #333}
.dots span.on{background:var(--red);border-color:var(--red)}

/* blog */
.blog{top:2493px;left:0;width:1200px;height:701px;background:#f4f4f4}
.post-card{left:112px;top:2695px;width:517px;height:328px;background:var(--white);box-shadow:0 2px 6px rgba(0,0,0,.12)}
.post-card-img{position:absolute;left:0;top:0;width:277px;height:328px;background:linear-gradient(135deg,#3b3227,#6b5a44 50%,#7f9a7a 70%,#3d352b)}
.post-card-body{position:absolute;left:289px;top:30px;width:220px}
.post-title{font-size:23px;line-height:31px;color:#222;font-weight:400}
.post-meta{font-size:12px;color:#444;margin-top:6px}
.post-meta em{font-style:normal;color:var(--red)}
.post-excerpt{font-size:12.5px;line-height:22px;color:#777;margin-top:16px}
.post-more{font-size:14px;color:var(--red);text-decoration:underline;margin-top:20px;display:block}
.mini-img{left:669px;width:100px;height:94px}
.mini-title{left:781px;font-size:16.5px;color:#222}
.mini-meta{left:781px;font-size:12px;color:#444}
.mini-meta em{font-style:normal;color:var(--red)}
.blog-btn{left:532px;top:3073px;width:136px;height:37px}

/* footer */
.footer{top:3194px;left:0;width:1200px;height:331px;background:linear-gradient(180deg,#1e1716,#2a1f1b)}
.footer-brand{left:0;top:3245px;width:1200px;display:flex;justify-content:center;align-items:center;gap:12px;font-size:42px;font-weight:900;color:#d9d9d9;letter-spacing:2px;line-height:1}
.footer-brand i{display:block;width:16px;height:16px;background:var(--red)}
.footer-nav{top:3345px;font-size:12px;color:#fff;letter-spacing:.8px;font-weight:600}
.social{top:3396px;left:501px;display:flex;gap:15px}
.social span{width:38px;height:38px;border-radius:50%;border:2px solid var(--red);display:block}
.footer-rule{top:3461px;left:0;width:1200px;height:1px;background:#4a3d38}
.copyright{top:3471px;left:0;width:1200px;text-align:center;font-size:11px;color:#cfcfcf}
</style>
</head>
<body>

<!-- top bar -->
<div class="abs topbar"></div>
<div class="abs contact-item" style="left:110px">
  <svg width="13" height="13" viewBox="0 0 24 24" fill="none" stroke="#555" stroke-width="2"><path d="M5 3h4l2 5-3 2a11 11 0 0 0 6 6l2-3 5 2v4a2 2 0 0 1-2 2A17 17 0 0 1 3 5a2 2 0 0 1 2-2z"/></svg>
  555-014-7845
</div>
<div class="abs contact-item" style="left:248px">
  <svg width="15" height="12" viewBox="0 0 24 18" fill="none" stroke="#555" stroke-width="2"><rect x="1" y="1" width="22" height="16"/><path d="M1 1l11 9 11-9"/></svg>
  torvane.us@mail.com
</div>
<div class="abs search">Search</div>
<div class="abs search-btn"><svg width="14" height="14" viewBox="0 0 24 24" fill="none" stroke="#fff" stroke-width="3"><circle cx="10" cy="10" r="7"/><path d="M15 15l7 7"/></svg></div>
<div class="abs account">
  <span><svg width="12" height="12" viewBox="0 0 24 24" fill="none" stroke="#fff" stroke-width="2"><path d="M14 3h7v18h-7M3 12h12M11 8l4 4-4 4"/></svg>SIGN IN</span>
  <span><svg width="14" height="12" viewBox="0 0 26 22" fill="none" stroke="#fff" stroke-width="2"><path d="M1 2h4l3 13h14l3-10H7"/><circle cx="10" cy="19" r="2"/><circle cx="20" cy="19" r="2"/></svg>CART: 0 ITEMS</span>
</div>

<!-- header -->
<div class="abs header"></div>
<div class="abs brand" style="top:53px"><i></i>US TORVANE</div>
<div class="abs brand-sub" style="top:87px">ustorvane.com</div>
<a class="abs nav active" style="left:435px;top:68px">HOME</a>
<a class="abs nav" style="left:536px;top:68px">PAGES</a>
<a class="abs nav" style="left:642px;top:68px">PRODUCTS</a>
<a class="abs nav" style="left:773px;top:68px">TESTIMONIALS</a>
<a class="abs nav" style="left:930px;top:68px">BLOG</a>
<a class="abs nav" style="left:1027px;top:68px">CONTACT</a>

<!-- hero -->
<div class="abs hero" role="img" aria-label="Close-up of a folding tactical knife, braided paracord, leather wallet and watch on a dark denim jacket"></div>
<h1 class="abs hero-title">U.S. TORVANE</h1>
<a class="abs btn hero-btn">Shop Now</a>

<!-- featured products -->
<div class="abs products"></div>
<h2 class="abs section-title" style="top:716px">Featured <em>Products</em></h2>
<p class="abs section-sub" style="top:764px">Lorem ipsum dolor sit amet consectetur adipiscing<br>elit sed do eiusmod tempor incididunt</p>

<svg class="abs arrow" style="left:108px" width="16" height="38" viewBox="0 0 16 38" fill="none" stroke="#444" stroke-width="1.5"><path d="M14 2L2 19l12 17"/></svg>
<svg class="abs arrow" style="left:1076px" width="16" height="38" viewBox="0 0 16 38" fill="none" stroke="#444" stroke-width="1.5"><path d="M2 2l12 17L2 36"/></svg>

<div class="abs product" style="left:176px">
  <div class="product-img" role="img" aria-label="Black tactical plate carrier vest" style="background:radial-gradient(circle,#555 0%,#2e2e2e 55%,#fff 72%)"></div>
  <div class="product-name">Consectetur Adipiscing<br>Seiuelit</div>
  <div class="stars"><svg width="76" height="12" viewBox="0 0 76 12"><g fill="#f2a900"><path id="s" d="M6 0l1.8 4 4.2.4-3.2 2.8 1 4.2L6 9.2 2.2 11.4l1-4.2L0 4.4 4.2 4z"/><use href="#s" x="16"/><use href="#s" x="32"/><use href="#s" x="48"/><use href="#s" x="64"/></g></svg></div>
  <div class="price">$98.00</div>
</div>
<div class="abs product" style="left:387px">
  <div class="product-img" role="img" aria-label="Camouflage tactical vest with magazine pouches" style="background:radial-gradient(circle,#7b7a4a 0%,#4f5230 55%,#fff 72%)"></div>
  <div class="product-name">Consectetur Adipiscing<br>Seiuelit</div>
  <div class="stars"><svg width="76" height="12" viewBox="0 0 76 12"><g fill="#f2a900"><use href="#s"/><use href="#s" x="16"/><use href="#s" x="32"/><use href="#s" x="48"/><use href="#s" x="64"/></g></svg></div>
  <div class="price">$98.00</div>
</div>
<div class="abs product" style="left:598px">
  <div class="product-img" role="img" aria-label="Black folding tactical knife" style="background:linear-gradient(180deg,#fff 38%,#3a3a3a 45%,#6a6a6a 55%,#fff 62%)"></div>
  <div class="product-name">Consectetur Adipiscing<br>Seiuelit</div>
  <div class="stars"><svg width="76" height="12" viewBox="0 0 76 12"><g fill="#f2a900"><use href="#s"/><use href="#s" x="16"/><use href="#s" x="32"/><use href="#s" x="48"/><use href="#s" x="64"/></g></svg></div>
  <div class="price">$98.00</div>
</div>
<div class="abs product" style="left:809px;border-right:none">
  <span class="badge">NEW</span>
  <div class="product-img" role="img" aria-label="Desert camouflage combat helmet" style="background:radial-gradient(circle at 50% 45%,#c9a77e 0%,#8a6a4a 40%,#2d3a2a 55%,#fff 70%)"></div>
  <div class="product-name">Consectetur Adipiscing<br>Seiuelit</div>
  <div class="stars"><svg width="76" height="12" viewBox="0 0 76 12"><g fill="#f2a900"><use href="#s"/><use href="#s" x="16"/><use href="#s" x="32"/><use href="#s" x="48"/><use href="#s" x="64"/></g></svg></div>
  <div class="price">$98.00</div>
</div>
<a class="abs btn" style="left:532px;top:1170px;width:136px;height:37px">View All</a>

<!-- who we are -->
<div class="abs about" role="img" aria-label="Folding knife with wooden handle, paracord bracelet and coins on blue denim"></div>
<h2 class="abs about-head" style="top:1362px;color:#fff">Who</h2>
<h2 class="abs about-head" style="top:1410px;color:var(--steel)">We Are</h2>
<p class="abs about-text">Sed ut perspiciatis undesesie soeiu omnis iste natus error sit voluptatem accusantium doloremque laudantium, totam rem aperiam, eaque ipsa quae ab illo inventore veritatis et quasi architecto beatae vitae dicta sunt explicabo. Nemo enim ipsam voluptatem quia voluptas sit aspernatur aut odit aut fugit, sed quia consequuntur magni dolores eos qui ratione voluptatem sequi nesciunt. Neque porro quisquam est, qui dolorem ipsum quia dolor sit amet, consectetur, adipisci velit, sed quia non numquam eius modi tempora incidunt ut labore et dolore magnam aliquam quaerat voluptatem. Ut enim ad minima veniam, quis nostrum exercitationem ullam</p>
<a class="abs btn about-btn">Read More</a>

<!-- testimonials -->
<div class="abs testimonials"></div>
<h2 class="abs section-title" style="top:1966px">Testimonials</h2>
<p class="abs section-sub" style="top:2014px">Lorem ipsum dolor sit amet consectetur adipiscing<br>elit sed do eiusmod tempor incididunt</p>

<div class="abs quote" style="left:111px">
  <p>"Sed ut perspiciatis undesesie soeiu omnis iste natus error sit seoi seinlvoluptatem accusantium doloremque laudantium, totam rem aperiam, eaque ipsa quae ab illo inventore veritatis et quasi archite ctout perspiciatisiu omnis"</p>
  <div class="person"><div class="avatar" role="img" aria-label="Customer portrait"></div><div><b>RANDALL</b><small>Customer</small></div></div>
</div>
<div class="abs quote" style="left:443px">
  <p>"Sed ut perspiciatis undesesie soeiu omnis iste natus error sit seoi seinlvoluptatem accusantium doloremque laudantium, totam rem aperiam, eaque ipsa quae ab illo inventore veritatis et quasi archite ctout perspiciatisiu omnis"</p>
  <div class="person"><div class="avatar" role="img" aria-label="Customer portrait" style="background:linear-gradient(160deg,#d8d2c8,#7a5e4a)"></div><div><b>RICHARDS</b><small>Customer</small></div></div>
</div>
<div class="abs quote" style="left:776px">
  <p>"Sed ut perspiciatis undesesie soeiu omnis iste natus error sit seoi seinlvoluptatem accusantium doloremque laudantium, totam rem aperiam, eaque ipsa quae ab illo inventore veritatis et quasi archite ctout perspiciatisiu omnis"</p>
  <div class="person"><div class="avatar" role="img" aria-label="Customer portrait" style="background:linear-gradient(160deg,#a9bcd0,#3d4a5c)"></div><div><b>BENZAMIN</b><small>Customer</small></div></div>
</div>
<div class="abs dots"><span class="on"></span><span></span><span></span><span></span></div>

<!-- blog -->
<div class="abs blog"></div>
<h2 class="abs section-title" style="top:2572px">Blog</h2>
<p class="abs section-sub" style="top:2621px">Lorem ipsum dolor sit amet consectetur adipiscing<br>elit sed do eiusmod tempor incididunt</p>

<article class="abs post-card">
  <div class="post-card-img" role="img" aria-label="Knife with sage green handle resting on a weathered log"></div>
  <div class="post-card-body">
    <h3 class="post-title">Ratione Voluptatem Eequi Tesciunt</h3>
    <p class="post-meta">Posted <em>February 6, 2020</em> By Jack Whisher</p>
    <p class="post-excerpt">Sed utse perspiciatis serundesesie soeiu omnis iste natus error sit seoi seinlvolupt atemaccusantium doloresek lseki mque laudantiume sersfmlsek dsd utperspicia atemaccusantium doloresek lseki</p>
    <a class="post-more">Read More</a>
  </div>
</article>

<div class="abs mini-img" style="top:2695px;background:linear-gradient(135deg,#c7b58a,#5a4b30 50%,#2a2a2a)" role="img" aria-label="Tactical watch and gloves"></div>
<h4 class="abs mini-title" style="top:2690px">Ratione Voluptatem Eequi Tesciunt</h4>
<p class="abs mini-meta" style="top:2720px">Posted <em>February 6, 2020</em> By Jack Whisher</p>

<div class="abs mini-img" style="top:2811px;background:linear-gradient(180deg,#d6b070,#8a7a45 45%,#5a3a22)" role="img" aria-label="Gear laid out in a field"></div>
<h4 class="abs mini-title" style="top:2807px">Ratione Voluptatem Eequi Tesciunt</h4>
<p class="abs mini-meta" style="top:2838px">Posted <em>February 6, 2020</em> By Jack Whisher</p>

<div class="abs mini-img" style="top:2928px;background:linear-gradient(160deg,#3a3a3a,#7a6650 50%,#4a3c30)" role="img" aria-label="Tactical boots on the ground"></div>
<h4 class="abs mini-title" style="top:2924px">Ratione Voluptatem Eequi Tesciunt</h4>
<p class="abs mini-meta" style="top:2955px">Posted <em>February 6, 2020</em> By Jack Whisher</p>

<a class="abs btn blog-btn">View All</a>

<!-- footer -->
<footer>
  <div class="abs footer"></div>
  <div class="abs footer-brand"><i></i>US TORVANE</div>
  <a class="abs footer-nav" style="left:315px">HOME</a>
  <a class="abs footer-nav" style="left:403px">PAGES</a>
  <a class="abs footer-nav" style="left:495px">PRODUCTS</a>
  <a class="abs footer-nav" style="left:610px">TESTIMONIALS</a>
  <a class="abs footer-nav" style="left:748px">BLOG</a>
  <a class="abs footer-nav" style="left:833px">CONTACT</a>
  <div class="abs social" aria-label="Social links"><span></span><span></span><span></span><span></span></div>
  <div class="abs footer-rule"></div>
  <p class="abs copyright">Copyright © 2020. All rights reserved.</p>
</footer>

</body>
</html>
```